Smile club flyer design

I am launching an office smile club and would like a design that sits my branding and that is appealing to customers. I have a design (I need a new one) that has all the information.
My website is maplehavendentalcarekx.com
Brand color is green. The design can be any color

Target Market(s)

Ages 30+

Industry/Entity Type

Dental

Font styles to use
Serif

Requirements
Must have
• Appealing to patients

```html
<!DOCTYPE html>
<html lang="en">
<head>
<meta charset="utf-8">
<title>Smile Club Membership</title>
<link href="https://fonts.googleapis.com/css2?family=Outfit:wght@300;400;600;700;800&display=swap" rel="stylesheet">
<style>
  :root {
    --sky-top: #9cc0ec;
    --sky-mid: #b9d4f3;
    --sky-low: #7fb0e6;
    --brand-green: #1d4a36;
    --ink: #111820;
    --ink-soft: #1f2a36;
    --cyan: #1fc6e6;
    --cyan-deep: #10b2d8;
    --teal: #27d3dc;
    --violet: #8d9cf0;
    --violet-deep: #7a86e8;
    --lime: #8ed61a;
    --lime-light: #b4ec3b;
    --glass: rgba(226, 240, 252, 0.72);
    --glass-edge: rgba(255, 255, 255, 0.85);
  }
  * { margin: 0; padding: 0; box-sizing: border-box; }
  html, body { width: 776px; height: 1200px; overflow: hidden; }
  body {
    position: relative;
    font-family: "Outfit", sans-serif;
    color: var(--ink);
    background:
      radial-gradient(ellipse at 80% 30%, rgba(255,255,255,0.45), transparent 55%),
      radial-gradient(ellipse at 20% 75%, rgba(255,255,255,0.35), transparent 50%),
      linear-gradient(180deg, var(--sky-top) 0%, var(--sky-mid) 45%, var(--sky-low) 100%);
  }
  .backdrop { position: absolute; inset: 0; }
  .title { position: absolute; top: 156px; left: 0; width: 776px; text-align: center; }
  .title-main { font-size: 50px; font-weight: 800; color: var(--brand-green); letter-spacing: 1px; line-height: 1; }
  .title-sub { font-size: 34px; font-weight: 300; letter-spacing: 4px; line-height: 1; margin-top: 10px; }

  .plan {
    position: absolute;
    border-radius: 30px;
    overflow: hidden;
    background: linear-gradient(170deg, var(--glass) 0%, rgba(205, 226, 248, 0.6) 100%);
    border: 2px solid var(--glass-edge);
    box-shadow: 0 6px 18px rgba(60, 110, 180, 0.25), inset 0 0 14px rgba(255,255,255,0.7);
    text-align: center;
  }
  .plan-band { position: absolute; top: 0; left: 0; width: 100%; }
  .plan-body { position: relative; }
  .plan-name { font-size: 19px; font-weight: 700; line-height: 1; }
  .plan-kind { font-size: 13px; font-weight: 600; letter-spacing: 0.5px; margin-top: 8px; }
  .plan-rule { height: 1px; background: var(--brand-green); opacity: 0.7; margin: 9px 12px 0; }
  .plan-price { font-size: 34px; font-weight: 700; line-height: 1; margin-top: 9px; }
  .plan-period { font-size: 11.5px; font-weight: 400; letter-spacing: 0.8px; margin-top: 24px; color: var(--ink-soft); }
  .perks { list-style: none; text-align: left; margin: 14px 0 0 18px; }
  .perk { position: relative; padding-left: 22px; font-size: 11.5px; font-weight: 600; line-height: 1.1; margin-bottom: 12px; letter-spacing: 0.2px; }
  .perk svg { position: absolute; left: 0; top: 0; width: 15px; height: 14px; }

  .plan-core { left: 53px; top: 325px; width: 207px; height: 350px; }
  .plan-bright { left: 287px; top: 325px; width: 207px; height: 350px; }
  .plan-total { left: 522px; top: 322px; width: 206px; height: 340px; }
  .plan-core .plan-body, .plan-bright .plan-body, .plan-total .plan-body { padding-top: 19px; }
  .plan-total .plan-body { padding-top: 17px; }

  .plan-refresh { left: 375px; top: 645px; width: 356px; height: 421px; z-index: 2; }
  .plan-refresh .plan-body { padding-top: 40px; }
  .plan-refresh .plan-name { font-size: 23px; line-height: 1.3; letter-spacing: 0.5px; }
  .plan-refresh .plan-rule { margin: 6px 52px 0; }
  .plan-refresh .plan-price { font-size: 44px; margin-top: 7px; }
  .plan-refresh .plan-period { font-size: 15px; margin-top: 24px; }
  .plan-refresh .perks { margin: 22px 0 0 55px; }
  .plan-refresh .perk { font-size: 18.5px; padding-left: 37px; line-height: 1.1; letter-spacing: 0.5px; }
  .plan-refresh .perk svg { width: 26px; height: 22px; top: 2px; }
  .offer { font-size: 16px; font-weight: 600; letter-spacing: 1px; margin-top: 40px; color: var(--ink-soft); }

  .join { position: absolute; left: 40px; width: 292px; text-align: center; font-weight: 700; }
  .join-head { top: 700px; font-size: 23px; line-height: 1.2; }
  .join-phone { top: 784px; font-size: 23px; line-height: 1.2; }
  .finance { position: absolute; left: 63px; top: 878px; font-size: 18px; font-weight: 700; line-height: 1.25; letter-spacing: 0.5px; }
  .payment { position: absolute; left: 63px; top: 973px; font-size: 17px; font-weight: 300; letter-spacing: 1px; }
  .fee { position: absolute; left: 63px; top: 1011px; font-size: 14px; font-weight: 300; font-style: italic; letter-spacing: 1px; }
  .tagline { position: absolute; top: 1097px; left: 0; width: 776px; text-align: center; font-size: 17px; font-weight: 300; letter-spacing: 1.5px; line-height: 1.12; }
</style>
</head>
<body>
  <div class="backdrop" role="img" aria-label="Soft blue background with flowing light streaks and sparkles"></div>

  <header class="title">
    <div class="title-main">SMILE CLUB</div>
    <div class="title-sub">MEMBERSHIP</div>
  </header>

  <svg width="0" height="0" style="position:absolute">
    <defs>
      <symbol id="tick" viewBox="0 0 30 26">
        <rect x="2" y="6" width="18" height="18" fill="none" stroke="#111820" stroke-width="3"/>
        <path d="M6 14 L11 20 L27 3" fill="none" stroke="#111820" stroke-width="3.6" stroke-linejoin="round"/>
      </symbol>
    </defs>
  </svg>

  <section class="plan plan-core">
    <svg class="plan-band" viewBox="0 0 207 140" height="140" preserveAspectRatio="none">
      <defs><linearGradient id="band-core" x1="0" y1="0" x2="0" y2="1"><stop offset="0" stop-color="var(--cyan-deep)"/><stop offset="1" stop-color="var(--cyan)"/></linearGradient></defs>
      <polygon points="0,0 207,0 207,93 104,136 0,93" fill="url(#band-core)"/>
    </svg>
    <div class="plan-body">
      <div class="plan-name">CORE CARE</div>
      <div class="plan-kind">PREVENTIVE</div>
      <div class="plan-rule"></div>
      <div class="plan-price">$39</div>
      <div class="plan-period">PER MONTH</div>
      <ul class="perks">
        <li class="perk"><svg><use href="#tick"/></svg>Comprehensive Annual Exam</li>
        <li class="perk"><svg><use href="#tick"/></svg>2 Professional Cleanings per Year</li>
        <li class="perk"><svg><use href="#tick"/></svg>Routine Bitewing X-rays</li>
        <li class="perk"><svg><use href="#tick"/></svg>10% Savings on Treatment</li>
      </ul>
    </div>
  </section>

  <section class="plan plan-bright">
    <svg class="plan-band" viewBox="0 0 207 140" height="140" preserveAspectRatio="none">
      <defs><linearGradient id="band-bright" x1="0" y1="0" x2="0" y2="1"><stop offset="0" stop-color="var(--violet-deep)"/><stop offset="1" stop-color="var(--violet)"/></linearGradient></defs>
      <polygon points="0,0 207,0 207,93 104,136 0,93" fill="url(#band-bright)"/>
    </svg>
    <div class="plan-body">
      <div class="plan-name">BRIGHT</div>
      <div class="plan-kind">COSMETIC</div>
      <div class="plan-rule"></div>
      <div class="plan-price">$59</div>
      <div class="plan-period">PER MONTH</div>
      <ul class="perks">
        <li class="perk"><svg><use href="#tick"/></svg>Annual In-Office Whitening (Top &amp; Bottom)</li>
        <li class="perk"><svg><use href="#tick"/></svg>Custom Whitening Trays</li>
        <li class="perk"><svg><use href="#tick"/></svg>15% Savings on Elective Treatment</li>
      </ul>
    </div>
  </section>

  <section class="plan plan-total">
    <svg class="plan-band" viewBox="0 0 206 140" height="140" preserveAspectRatio="none">
      <defs><linearGradient id="band-total" x1="0" y1="0" x2="0" y2="1"><stop offset="0" stop-color="var(--cyan-deep)"/><stop offset="1" stop-color="var(--teal)"/></linearGradient></defs>
      <polygon points="0,0 206,0 206,93 103,136 0,93" fill="url(#band-total)"/>
    </svg>
    <div class="plan-body">
      <div class="plan-name">TOTAL SMILE</div>
      <div class="plan-kind">PERIODONTAL</div>
      <div class="plan-rule"></div>
      <div class="plan-price">$89</div>
      <div class="plan-period">PER MONTH</div>
      <ul class="perks">
        <li class="perk"><svg><use href="#tick"/></svg>4-3 Perio Maintenance Visits per Year</li>
        <li class="perk"><svg><use href="#tick"/></svg>1 Comprehensive Exam</li>
        <li class="perk"><svg><use href="#tick"/></svg>Diagnostic X-rays</li>
        <li class="perk"><svg><use href="#tick"/></svg>15% Savings on Restorative &amp; Elective Care</li>
      </ul>
    </div>
  </section>

  <section class="plan plan-refresh">
    <svg class="plan-band" viewBox="0 0 356 190" height="190" preserveAspectRatio="none">
      <defs><linearGradient id="band-refresh" x1="0" y1="0" x2="0" y2="1"><stop offset="0" stop-color="var(--lime)"/><stop offset="1" stop-color="var(--lime-light)"/></linearGradient></defs>
      <polygon points="0,0 356,0 356,126 178,182 0,126" fill="url(#band-refresh)"/>
    </svg>
    <div class="plan-body">
      <div class="plan-name">SMILE<br>REFRESH PACKAGE</div>
      <div class="plan-rule"></div>
      <div class="plan-price">$499</div>
      <div class="plan-period">PER MONTH</div>
      <ul class="perks">
        <li class="perk"><svg><use href="#tick"/></svg>Cleaning +<br>Comprehensive Exam<br>+ Whitening</li>
      </ul>
      <div class="offer">LIMITED TIME OFFER</div>
    </div>
  </section>

  <div class="join join-head">JOIN SMILE CLUB<br>TODAY!</div>
  <div class="join join-phone">PHONE:<br>7800-555-0142</div>
  <div class="finance">FLEXIBLE FINANCING FOR<br>TREATMENT:</div>
  <div class="payment">PAYMENT PLANS AVAILABLE</div>
  <div class="fee">*$49 LIFETIME ACTIVATION FEE</div>

  <footer class="tagline">AFFORDABLE DENTAL CARE<br>NO INSURANCE REQUIRED</footer>
</body>
</html>
```